Plakat-Design für kleine deutsche Immobilien- und Reiseveranstalter-Firma
Zielgruppe
Kleine deutsche Immobilien- und Reiseveranstalter-Firma, spezialisiert auf Italien. In Italien sind es Immobilienbesitzer, die aus versch. Gründen hoffen an Ausländer zu verkaufen/vermieten ( Alter ca. ab 35-40)
Aufgabenstellung
Um neue Immo-Besitzer anzusprechen, lassen wir in verschiedenen Gemeinden in der Nordtoskana Plakate gegen Gebühr kleben ( 70 x 100, meistens 1 bis 2 Wochen)
Text auf Italienisch
Was an Text rein muss( falls Sie es anders mitteilen wollen, bin ich gerne bereit es zu diskutieren)
VUOI VENDERE CASA A STRANIERI O AFFITTARLA A TURISTI ? (Übersetzung ca.:= wollen Sie Ihre Immobilie an Ausländer verkaufen oder an Touristen vermieten?)
Verdona
Germania – info@verdona-beispiel.de + 49 7412 3810457
Italia – 0571 – 394062, Cell.: 371 – 2094716, 335- 47 92608,
www.verdonacase-beispiel.com
www.verdonaaffitti-beispiel.com
Der Poster, den man meistens im Vorbeifahren sieht, soll springt sofort ins Auge , fast aufdringlich. Man kann mit Farben oder Bildern (oder beiden) arbeiten. Stechende Farben, sonst minimalistisch einfach. (??)
Erfahrung zeigt, daß die beiden Mobile Nummern (Cell.:) mehr sichtbar sein könnten. Ich kann zwei letzte zeigen, aber ungern, weil sie mir nicht gefallen und Neues – besseres suche.
PS: habe mal so was wie Guerilla -Marketing versucht – wurde nicht verstanden.
Bilder kann ich nach Wunsch liefern.

```html
<!DOCTYPE html>
<html lang="it">
<head>
<meta charset="utf-8">
<title>Verdona – Vuoi vendere casa</title>
<link href="https://fonts.googleapis.com/css2?family=Montserrat:ital,wght@0,700;0,800;0,900;1,800;1,900&display=swap" rel="stylesheet">
<style>
  :root {
    --backdrop: #566f8c;
    --white: #ffffff;
    --green: #2db34a;
    --green-dark: #1f8f45;
    --red: #ec3b3f;
    --ink: #1c1a1b;
    --footer: #1c3335;
    --shadow-mint: #c9dcc6;
  }
  * { margin: 0; padding: 0; box-sizing: border-box; }
  html, body {
    width: 1200px; height: 1177px; overflow: hidden;
    background: var(--backdrop);
    font-family: "Montserrat", Arial, sans-serif;
  }
  .poster {
    position: absolute; left: 198px; top: 20px;
    width: 804px; height: 1137px;
    background: var(--white);
    overflow: hidden;
  }
  .photo {
    position: absolute; left: 0; top: 0; width: 804px; height: 560px;
    background: linear-gradient(180deg, #dfe7ee 0%, #c9d8e2 18%, #5e7d46 30%, #c8ae8a 48%, #b88c63 62%, #7b7a48 82%, #3f6b2f 100%);
  }
  .shapes { position: absolute; inset: 0; }
  .brand {
    position: absolute; left: 74px; top: 48px;
    display: flex; align-items: center; gap: 12px;
  }
  .brand-dot { width: 36px; height: 36px; border-radius: 50%; background: var(--green); }
  .brand-name { font-weight: 800; font-size: 52px; color: var(--ink); letter-spacing: -0.5px; }
  .headline {
    position: absolute; transform: translate(-50%, -50%) rotate(-4deg);
    color: var(--white); font-weight: 900; font-style: italic;
    white-space: nowrap; line-height: 1; text-transform: uppercase;
    text-shadow: 2px 2px 0 rgba(0,0,0,0.12);
  }
  .headline--big { font-size: 74px; letter-spacing: -1px; }
  .headline--sub { font-size: 39px; font-weight: 800; }
  .cta-text {
    position: absolute; left: 403px; top: 769px;
    transform: translate(-50%, -50%) rotate(-4deg);
    color: var(--white); font-weight: 900; font-style: italic;
    font-size: 64px; white-space: nowrap; line-height: 1;
    text-shadow: 3px 3px 0 rgba(0,0,0,0.15);
  }
  .phone-number {
    position: absolute; font-weight: 800; font-size: 56px;
    color: var(--ink); line-height: 1; letter-spacing: -0.5px;
  }
  .phone-tag {
    position: absolute; color: var(--white); font-weight: 800;
    font-size: 17px; line-height: 1; transform: translate(-50%, -50%);
  }
  .footer {
    position: absolute; left: 0; top: 1068px; width: 804px; height: 69px;
    background: var(--footer);
  }
  .contact-icon {
    position: absolute; width: 30px; height: 30px; border-radius: 50%;
    background: var(--green); border: 3px solid var(--white);
    transform: translate(-50%, -50%);
    display: flex; align-items: center; justify-content: center;
  }
  .contact-text {
    position: absolute; top: 1102px; transform: translate(-50%, -50%);
    color: var(--white); font-weight: 800; font-size: 12.5px; white-space: nowrap;
  }
</style>
</head>
<body>
<div class="poster">
  <div class="photo" role="img" aria-label="Foto di una villa toscana con portici, tetti in cotto e cipressi nel giardino"></div>

  <svg class="shapes" width="804" height="1137" viewBox="0 0 804 1137">
    <defs>
      <linearGradient id="bandGreen" x1="0" y1="0" x2="0" y2="1">
        <stop offset="0" stop-color="#1f8f45"/>
        <stop offset="1" stop-color="#2db34a"/>
      </linearGradient>
    </defs>
    <!-- brand corner -->
    <polygon points="0,0 396,0 366,66 327,145 0,169" fill="var(--white)"/>
    <polygon points="366,66 327,145 0,169 0,176 352,156" fill="var(--green)"/>
    <!-- white lower field under the photo -->
    <polygon points="0,790 804,737 804,1137 0,1137" fill="var(--white)"/>
    <!-- headline band -->
    <polygon points="0,539 258,526 264,466 574,437 564,499 804,486 804,739 0,792" fill="url(#bandGreen)"/>
    <!-- call to action -->
    <g transform="rotate(-4 403 769)">
      <rect x="77" y="729" width="664" height="92" rx="14" fill="var(--shadow-mint)"/>
      <polygon points="398,816 432,816 420,840" fill="var(--shadow-mint)"/>
      <rect x="69" y="719" width="664" height="92" rx="14" fill="var(--red)"/>
      <polygon points="392,809 428,809 414,832" fill="var(--red)"/>
    </g>
    <!-- phone rows -->
    <rect x="61" y="927" width="560" height="4" fill="var(--green-dark)"/>
    <polygon points="626,872 749,872 735,933 610,933" fill="var(--green)"/>
    <rect x="61" y="1019" width="476" height="4" fill="var(--green-dark)"/>
    <polygon points="540,964 664,964 650,1025 524,1025" fill="var(--green)"/>
    <!-- phone handsets -->
    <g fill="var(--red)">
      <path d="M60,873 c4,-3 8,-2 10,1 l6,10 c1,3 0,6 -3,8 l-4,3 c3,8 9,15 17,19 l3,-4 c2,-3 5,-3 8,-2 l9,6 c3,2 3,6 1,9 l-4,5 c-4,3 -10,3 -16,0 c-15,-8 -26,-21 -32,-37 c-2,-6 -1,-11 5,-15z"/>
      <path d="M60,964 c4,-3 8,-2 10,1 l6,10 c1,3 0,6 -3,8 l-4,3 c3,8 9,15 17,19 l3,-4 c2,-3 5,-3 8,-2 l9,6 c3,2 3,6 1,9 l-4,5 c-4,3 -10,3 -16,0 c-15,-8 -26,-21 -32,-37 c-2,-6 -1,-11 5,-15z"/>
    </g>
  </svg>

  <div class="brand">
    <span class="brand-dot"></span>
    <span class="brand-name">Verdona</span>
  </div>

  <div class="headline headline--big" style="left:409px; top:500px;">Vuoi</div>
  <div class="headline headline--big" style="left:408px; top:578px;">Vendere casa</div>
  <div class="headline headline--sub" style="left:407px; top:644px;">A stranieri o affittarla</div>
  <div class="headline headline--sub" style="left:406px; top:687px;">A turisti ?</div>

  <div class="cta-text">CHIAMARE ORA</div>

  <div class="phone-number" style="left:115px; top:872px;">0741-23810457</div>
  <div class="phone-tag" style="left:680px; top:903px;">Germania</div>
  <div class="phone-number" style="left:108px; top:964px;">0571–394062</div>
  <div class="phone-tag" style="left:594px; top:995px;">Verdona</div>

  <div class="footer"></div>
  <div class="contact-icon" style="left:126px; top:1068px;">
    <svg width="14" height="10" viewBox="0 0 14 10"><rect x="0.7" y="0.7" width="12.6" height="8.6" fill="none" stroke="#fff" stroke-width="1.4"/><path d="M1,1 L7,6 L13,1" fill="none" stroke="#fff" stroke-width="1.4"/></svg>
  </div>
  <div class="contact-icon" style="left:353px; top:1068px;">
    <svg width="14" height="14" viewBox="0 0 14 14" fill="none" stroke="#fff" stroke-width="1.3"><circle cx="7" cy="7" r="6"/><ellipse cx="7" cy="7" rx="2.6" ry="6"/><path d="M1,7 H13 M2,4 H12 M2,10 H12"/></svg>
  </div>
  <div class="contact-icon" style="left:626px; top:1068px;">
    <svg width="14" height="14" viewBox="0 0 14 14" fill="none" stroke="#fff" stroke-width="1.3"><circle cx="7" cy="7" r="6"/><ellipse cx="7" cy="7" rx="2.6" ry="6"/><path d="M1,7 H13 M2,4 H12 M2,10 H12"/></svg>
  </div>
  <div class="contact-text" style="left:126px;">info@verdona-beispiel.de</div>
  <div class="contact-text" style="left:370px;">www.verdonacase-beispiel.com</div>
  <div class="contact-text" style="left:646px;">www.verdonaaffitti-beispiel.com</div>
</div>
</body>
</html>
```